Realty Group Needs Classy, Contemporary Letterhead Design

We need a letterhead design for a new realty company located in NY, USA. We buy investment properties to rehabilitate and or keep in our rental portfolio.

```html
<!DOCTYPE html>
<html lang="en">
<head>
<meta charset="utf-8">
<title>Meridian Realty Group – Letterhead</title>
<link href="https://fonts.googleapis.com/css2?family=Mulish:wght@400;800&family=Roboto:wght@400&display=swap" rel="stylesheet">
<style>
  :root {
    --purple: #4e2d84;
    --grey-line: #9a9a9a;
    --ink: #222222;
    --ink-soft: #3a3a3a;
    --rule: #6d6d6d;
    --backdrop: #dcdcdc;
    --paper: #ffffff;
  }
  * { margin: 0; padding: 0; box-sizing: border-box; }
  html, body { width: 1077px; height: 1200px; overflow: hidden; background: var(--backdrop); }
  .letterhead {
    position: absolute; left: 113px; top: 0;
    width: 850px; height: 1200px;
    background: var(--paper);
    font-family: "Mulish", sans-serif;
    color: var(--ink);
  }
  .brand {
    position: absolute; left: 53px; top: 106px;
    font-weight: 800; font-size: 27px; color: var(--purple);
    display: flex; align-items: center; gap: 10px;
  }
  .brand-dot { width: 16px; height: 16px; border-radius: 50%; background: var(--purple); }
  .header-rule { position: absolute; left: 538px; top: 73px; width: 2px; height: 102px; background: var(--rule); }
  .contact {
    position: absolute; left: 567px; top: 69px;
    font-family: "Roboto", sans-serif; font-size: 17px; line-height: 21px; color: var(--ink-soft);
    list-style: none;
  }
  .contact .address { margin-bottom: 3px; }
  .contact li { display: flex; align-items: center; gap: 6px; }
  .contact svg { width: 14px; height: 14px; fill: var(--purple); flex: none; }
  .recipient {
    position: absolute; left: 53px; top: 296px;
    font-size: 15px; line-height: 21.4px; font-style: normal;
  }
  .body-copy {
    position: absolute; left: 53px; top: 393px; width: 752px;
    font-size: 15.2px; line-height: 24.3px; text-align: justify;
  }
  .body-copy p + p { margin-top: 26px; }
  .body-copy p.tight { margin-top: 22px; }
  .closing { position: absolute; left: 53px; top: 800px; font-size: 16.5px; }
  .signature {
    position: absolute; left: 53px; top: 832px; width: 155px; height: 66px;
    background: linear-gradient(90deg, #efefef, #f7f7f7);
  }
  .footer-band { position: absolute; left: 0; bottom: 0; width: 850px; height: 80px; }
  .website {
    position: absolute; left: 53px; top: 1160px;
    display: flex; align-items: center; gap: 7px;
    font-family: "Roboto", sans-serif; font-size: 16.5px; color: #ffffff;
  }
  .website svg { width: 14px; height: 14px; }
</style>
</head>
<body>
<main class="letterhead">
  <div class="brand"><span class="brand-dot"></span>Meridian Realty Group, LLC</div>

  <div class="header-rule"></div>
  <ul class="contact">
    <li class="address">48 Harbor Lane, Suite 210<br>Albany, NY, USA</li>
    <li>
      <svg viewBox="0 0 24 24"><path d="M6.6 10.8a15.1 15.1 0 0 0 6.6 6.6l2.2-2.2c.3-.3.7-.4 1-.2 1.1.4 2.3.6 3.6.6.6 0 1 .4 1 1V20c0 .6-.4 1-1 1A17 17 0 0 1 3 4c0-.6.4-1 1-1h3.5c.6 0 1 .4 1 1 0 1.3.2 2.5.6 3.6.1.3 0 .7-.2 1z"/></svg>
      555-201-3847
    </li>
    <li>
      <svg viewBox="0 0 24 24"><path d="M6 2h12v5H6zM3 8h18a2 2 0 0 1 2 2v7h-4v5H5v-5H1v-7a2 2 0 0 1 2-2zm4 8v4h10v-4z"/></svg>
      555-201-3850
    </li>
    <li>
      <svg viewBox="0 0 24 24"><path d="M2 5h20v14H2zm2 2v.5l8 5.5 8-5.5V7l-8 5.5z"/></svg>
      hello@meridianrealtyllc.com
    </li>
  </ul>

  <address class="recipient">
    Mr/s<br>First Name and Last Name<br>Company Name<br>Address
  </address>

  <section class="body-copy">
    <p>Lorem Ipsum is simply dummy text of the printing and typesetting industry. Lorem Ipsum has been the industry's standard dummy text ever since the 1500s, when an unknown printer took a galley of type and scrambled it to make a type specimen book. It has survived not only five centuries, but also the leap into electronic typesetting, remaining essentially unchanged. It was popularised in the 1960s with the release of Printset sheets containing Lorem Ipsum passages.</p>
    <p>he standard chunk of Lorem Ipsum used since the 1500s is reproduced below for those interested. Sections 1.10.32 and 1.10.33 from "de Rebus Variis" by an early author are also reproduced in their exact original form, accompanied by English versions from the 1914 translation by J. Pellow. Lorem ipsum dolor sit amet, consectetur adipiscing elit, sed do eiusmod tempor incididunt ut labore et dolore magna aliqua.</p>
    <p class="tight">It is a long established fact that a reader will be distracted by the readable content of a page when looking at its layout. The point of using Lorem Ipsum is that it has a more-or-less normal distribution of letters, as opposed to using 'Content here, content here', making it look like readable English. Many desktop publishing packages and web page editors now .</p>
  </section>

  <p class="closing">Your Sincerely,</p>
  <div class="signature" role="img" aria-label="Handwritten signature"></div>

  <svg class="footer-band" viewBox="0 0 850 80" preserveAspectRatio="none" aria-hidden="true">
    <path fill="none" stroke="var(--grey-line)" stroke-width="3" d="M0,14 Q425,-6 850,14"/>
    <path fill="var(--purple)" d="M0,26 Q425,6 850,26 L850,80 L0,80 Z"/>
  </svg>

  <div class="website">
    <svg viewBox="0 0 24 24"><circle cx="12" cy="12" r="10" fill="none" stroke="#fff" stroke-width="2"/><path d="M2 12h20M12 2c3 3 3 17 0 20M12 2c-3 3-3 17 0 20" fill="none" stroke="#fff" stroke-width="1.6"/></svg>
    www.meridianrealtyllc.com
  </div>
</main>
</body>
</html>
```